Business Card - connecting 2 souls and beggining the journey of self discovery

Logo on the front
with tag line

On the back list of services and contact details

Seminars
workshops
Coaching
podcasts

Darren Whitlow
Health & Wellbeing Life Coach
0491 372 615
darren@brightcoreliving.example
brightcoreliving.example

Industry/Entity Type

Life Coaching

Contact Information for Business Card

I like the use of colour from the logo to be used. I'm not a fan of white.

Requirements
Must have
• My tagline: The journey home starts with you
Nice to have
• Use of colour that is in the mind body soul logo

```html
<!DOCTYPE html>
<html lang="en">
<head>
<meta charset="utf-8">
<title>Bright Core Living – Business Card</title>
<link href="https://fonts.googleapis.com/css2?family=Roboto:wght@400;500&display=swap" rel="stylesheet">
<style>
  :root {
    --page: #e8e5e1;
    --card: #2f2f2f;
    --text: #f2f2f2;
    --name-green: #8dc63f;
    --accent-orange: #f39a4b;
    --mark-coral: #f0766a;
  }
  * { margin: 0; padding: 0; box-sizing: border-box; }
  html, body { width: 1200px; height: 1200px; overflow: hidden; }
  body {
    background: var(--page);
    font-family: "Roboto", Arial, sans-serif;
    color: var(--text);
    position: relative;
  }
  .card {
    position: absolute;
    left: 214px;
    width: 772px;
    height: 440px;
    background: var(--card);
    border-radius: 18px;
  }
  .card--front { top: 150px; }
  .card--back { top: 635px; }

  .brand {
    position: absolute;
    display: flex;
    flex-direction: column;
    align-items: center;
    transform: translateX(-50%);
  }
  .brand__dot {
    border-radius: 50%;
    background: var(--mark-coral);
  }
  .brand__name {
    font-weight: 500;
    color: var(--text);
    white-space: nowrap;
    letter-spacing: -0.3px;
  }
  .card--front .brand { left: 203px; top: 150px; }
  .card--front .brand__dot { width: 52px; height: 52px; margin-bottom: 30px; }
  .card--front .brand__name { font-size: 27px; }
  .card--back .brand { left: 386px; top: 108px; }
  .card--back .brand__dot { width: 64px; height: 64px; margin-bottom: 44px; }
  .card--back .brand__name { font-size: 32px; }

  .divider {
    position: absolute;
    left: 387px;
    top: 100px;
    width: 2px;
    height: 240px;
    background: var(--accent-orange);
    opacity: 0.8;
  }
  .details {
    position: absolute;
    left: 422px;
    top: 92px;
  }
  .details__name {
    font-size: 29px;
    font-weight: 500;
    color: var(--name-green);
    line-height: 34px;
  }
  .details__title {
    font-size: 20px;
    line-height: 26px;
  }
  .details__address {
    margin-top: 14px;
    font-size: 19px;
    line-height: 27px;
  }
  .contact-list {
    list-style: none;
    margin-top: 12px;
  }
  .contact-list li {
    display: flex;
    align-items: center;
    font-size: 19px;
    line-height: 28px;
  }
  .contact-list svg {
    width: 17px;
    height: 17px;
    margin-right: 8px;
    fill: none;
    stroke: var(--accent-orange);
    stroke-width: 1.6;
  }
  .services {
    position: absolute;
    left: 0;
    right: 0;
    top: 394px;
    text-align: center;
    font-size: 20px;
  }
  .services__sep {
    display: inline-block;
    width: 8px;
    height: 8px;
    border-radius: 50%;
    background: var(--accent-orange);
    margin: 0 9px;
    vertical-align: middle;
  }
  .tagline {
    position: absolute;
    left: 0;
    right: 0;
    top: 378px;
    text-align: center;
    font-size: 23px;
    letter-spacing: 0.2px;
  }
</style>
</head>
<body>
  <section class="card card--front">
    <div class="brand">
      <span class="brand__dot"></span>
      <span class="brand__name">Bright Core Living</span>
    </div>
    <div class="divider"></div>
    <div class="details">
      <p class="details__name">Darren Whitlow</p>
      <p class="details__title">Health &amp; Wellbeing Life Coach</p>
      <p class="details__address">2280 Alder Lane, Suite 14<br>Fairview, CA 3071</p>
      <ul class="contact-list">
        <li><svg viewBox="0 0 20 20"><path d="M4 2.5l3 .5 1.2 3.5-2 1.5a10 10 0 0 0 5.8 5.8l1.5-2 3.5 1.2.5 3c-.3 1-1.2 1.5-2.2 1.5C8.5 17 3 11.5 2.5 4.7 2.5 3.7 3 2.8 4 2.5z"/></svg>0491 372 615</li>
        <li><svg viewBox="0 0 20 20"><rect x="5" y="1.5" width="10" height="17" rx="1.5"/><line x1="9" y1="15.5" x2="11" y2="15.5"/></svg>000-000-0000</li>
        <li><svg viewBox="0 0 20 20"><rect x="1.5" y="4" width="17" height="12"/><path d="M1.5 4l8.5 7 8.5-7"/></svg>darren@brightcoreliving.example</li>
        <li><svg viewBox="0 0 20 20"><circle cx="10" cy="10" r="8"/><ellipse cx="10" cy="10" rx="3.5" ry="8"/><line x1="2" y1="10" x2="18" y2="10"/><path d="M3.5 5.5h13M3.5 14.5h13"/></svg>www.brightcoreliving.example</li>
      </ul>
    </div>
    <p class="services">Seminars<span class="services__sep"></span>workshops<span class="services__sep"></span>Coaching<span class="services__sep"></span>podcasts</p>
  </section>

  <section class="card card--back">
    <div class="brand">
      <span class="brand__dot"></span>
      <span class="brand__name">Bright Core Living</span>
    </div>
    <p class="tagline">The journey home starts with you</p>
  </section>
</body>
</html>
```